Private Investment Firm Needs PowerPoint Presentation Template

Design PowerPoint template, take Pinebrook-submitted rough presentation draft, and drop it into new template. See attached Project Brief file for more detail.
Updates

Some decent designs have been submitted but they seem to lack the understanding of our target markets. I am hopeful that more time and feedback will result in better results.

Target Market(s)

Private company owners and intermediaries.

Font styles to use
Serif

Colors
3176b5

Requirements
Must have
• See attached Project Brief.
Nice to have
Should not have
• No B2C fluff--this is a B2B project.

```html
<!DOCTYPE html>
<html lang="en">
<head>
<meta charset="utf-8">
<title>Pinebrook Representative Non-Control Capital Investments</title>
<link href="https://fonts.googleapis.com/css2?family=Montserrat:wght@400;500;600;700&family=Libre+Baskerville&display=swap" rel="stylesheet">
<style>
  :root {
    --brand-blue: #0070c0;
    --title-blue: #1170c4;
    --bar-blue: #0a6fc1;
    --white: #ffffff;
    --ink-navy: #1c3f8f;
    --client-red: #d8302e;
    --photo-light: #eef1f3;
    --photo-mid: #dfe4e8;
  }
  * { margin: 0; padding: 0; box-sizing: border-box; }
  html, body { width: 1200px; height: 676px; overflow: hidden; background: var(--white); }
  .slide {
    position: relative; width: 1200px; height: 676px; overflow: hidden;
    background: var(--white); font-family: "Montserrat", sans-serif;
  }
  .side-bar-left { position: absolute; left: 0; top: 0; width: 44px; height: 676px; background: var(--bar-blue); }
  .side-bar-right { position: absolute; right: 0; top: 0; width: 12px; height: 676px; background: var(--bar-blue); }
  .site-url {
    position: absolute; left: 22px; top: 336px;
    transform: translate(-50%, -50%) rotate(-90deg);
    font-family: "Libre Baskerville", serif; font-size: 13px; color: var(--white);
    white-space: nowrap; letter-spacing: 0.2px;
  }
  .page-number {
    position: absolute; left: 1158px; top: 18px;
    font-family: "Libre Baskerville", serif; font-size: 16px; color: #333;
  }
  .architecture-photo {
    position: absolute; left: 580px; top: 300px; width: 608px; height: 376px;
    background: linear-gradient(105deg, rgba(255,255,255,1) 0%, var(--photo-light) 40%, var(--photo-mid) 75%, var(--photo-light) 100%);
  }
  .section-title {
    position: absolute; left: 86px; top: 82px;
    font-size: 28px; line-height: 33px; font-weight: 600; color: var(--title-blue);
    letter-spacing: 0.3px;
  }
  .case-panel {
    position: absolute; left: 45px; top: 176px; width: 859px; height: 406px;
    background: var(--brand-blue); color: var(--white);
  }
  .case-heading {
    position: absolute; left: 41px; top: 16px;
    font-size: 41px; font-weight: 600; letter-spacing: 0.4px;
  }
  .case-points { position: absolute; left: 41px; top: 80px; width: 800px; list-style: none; }
  .case-points li {
    position: relative; padding-left: 32px; margin-bottom: 28px;
    font-size: 16.8px; line-height: 28px; font-weight: 400;
  }
  .case-points li::before {
    content: ""; position: absolute; left: 5px; top: 10px;
    width: 10px; height: 10px; background: var(--white);
    box-shadow: inset 0 0 0 2px var(--brand-blue), 0 0 0 1px var(--white);
  }
  .firm-mark {
    position: absolute; left: 68px; top: 612px; display: flex; align-items: center; gap: 9px;
  }
  .firm-mark .dot { width: 34px; height: 34px; border-radius: 50%; background: var(--ink-navy); }
  .firm-mark .name {
    font-family: "Libre Baskerville", serif; font-size: 17px; color: var(--ink-navy); letter-spacing: 1px;
  }
  .client-mark {
    position: absolute; left: 940px; top: 582px;
    font-family: "Montserrat", sans-serif; font-weight: 700; font-size: 22px;
    color: var(--client-red); letter-spacing: 1px;
  }
</style>
</head>
<body>
<div class="slide">
  <div class="architecture-photo" role="img" aria-label="Faded photograph of white modern architectural columns and glass facade"></div>
  <div class="side-bar-left"></div>
  <div class="side-bar-right"></div>
  <div class="site-url">www.pinebrookcapital.com</div>
  <div class="page-number">16</div>

  <h1 class="section-title">PINEBROOK REPRESENTATIVE NON-CONTROL<br>CAPITAL INVESTMENTS</h1>

  <section class="case-panel">
    <h2 class="case-heading">Family Ownership &amp; Wealth Transfer</h2>
    <ul class="case-points">
      <li>Provider of fire and security alarm design, installation, service, and monitoring services for commercial and residential end-markets.</li>
      <li>Pinebrook’s capital allowed for enough cash breathing room for the CEO to think strategically about the business, focus on the growth of the Company, and build family wealth. Five years later, after the Company and Pinebrook were successful in substantially growing the business, Ridgeline Alarm bought out Pinebrook’s ownership position entirely with senior debt—as a result, the CEO (father), COO (son), and key management team were back to owning 100% of the Company. The son had a significantly larger stake in the business than five years earlier and the father had the flexibility to work through his family estate plans.</li>
    </ul>
  </section>

  <div class="firm-mark">
    <span class="dot"></span>
    <span class="name">PINEBROOK CAPITAL</span>
  </div>

  <div class="client-mark">RIDGELINE ALARM</div>
</div>
</body>
</html>
```